BOLD & MINIMALIST DESIGN NEEDED

We want a very bold but minimalistic business card design that is impactful and utilizes both sides of the business card. Our current logo is included for your use.

We want bold fonts and good use of negative space. We don't want the logo to overpower the design.

Target Market(s)

Professionals who are building new commercial buildings.

Industry/Entity Type

Construction

Contact Information for Business Card

Name, Title, email, office phone, cell phone, website

Font styles to use
Serif
Sans Serif

Requirements
Must have
• Bold design!

```html
<!DOCTYPE html>
<html lang="en">
<head>
<meta charset="utf-8">
<title>Ridgemont – Business Card</title>
<link rel="stylesheet" href="https://fonts.googleapis.com/css2?family=PT+Sans:wght@700&family=Poppins:wght@400;700&display=swap">
<style>
  :root {
    --stage: #ababab;
    --paper: #ffffff;
    --ink: #0a0b0d;
    --green: #86c524;
    --green-light: #b8e07a;
    --white: #f4f3f1;
  }
  * { box-sizing: border-box; margin: 0; padding: 0; }
  html, body { width: 1093px; height: 1200px; overflow: hidden; }
  body {
    background: var(--stage);
    font-family: "Poppins", sans-serif;
    position: relative;
  }
  .card {
    position: absolute;
    left: 264px;
    border-radius: 24px;
    overflow: hidden;
  }
  .card-front { top: 226px; width: 578px; height: 357px; background: var(--paper); }
  .card-back  { top: 621px; width: 584px; height: 358px; background: var(--ink); }

  .edge-band {
    position: absolute;
    left: 0; right: 0; bottom: 0;
    height: 8px;
    background: linear-gradient(90deg, var(--green) 0%, var(--green) 50%, var(--green-light) 58%, var(--green-light) 100%);
  }

  .holder { position: absolute; left: 0; top: 42px; padding-left: 26px; }
  .holder::before {
    content: ""; position: absolute; left: 0; top: 0;
    width: 17px; height: 36px; background: var(--green);
  }
  .holder-name {
    font-family: "PT Sans", sans-serif; font-weight: 700;
    font-size: 23px; line-height: 24px; color: var(--ink); letter-spacing: 0.2px;
  }
  .holder-title { font-size: 16px; line-height: 18px; color: var(--green); }

  .brand {
    position: absolute;
    display: flex; align-items: center; gap: 10px;
    font-family: "PT Sans", sans-serif; font-weight: 700;
    text-transform: uppercase;
  }
  .brand-mark { display: block; background: var(--green); }
  .card-front .brand { left: 310px; top: 120px; font-size: 36px; color: var(--ink); letter-spacing: 0.5px; }
  .card-front .brand-mark { width: 22px; height: 22px; }
  .card-back .brand { left: 50%; top: 50%; transform: translate(-50%, -50%); font-size: 52px; color: var(--white); letter-spacing: 1px; }
  .card-back .brand-mark { width: 32px; height: 32px; }

  .contacts {
    position: absolute; bottom: 34px;
    font-size: 17px; line-height: 21px; color: var(--ink);
    list-style: none;
  }
  .contacts li { display: flex; align-items: center; gap: 8px; }
  .contacts svg { width: 14px; height: 14px; flex: none; }
  .contacts-phone { left: 26px; }
  .contacts-web { right: 25px; text-align: right; }
  .contacts-web li { justify-content: flex-end; }
</style>
</head>
<body>
  <section class="card card-front" aria-label="Card front">
    <div class="holder">
      <p class="holder-name">MARCUS HALE</p>
      <p class="holder-title">Managing Director</p>
    </div>

    <div class="brand"><span class="brand-mark"></span>Ridgemont</div>

    <ul class="contacts contacts-phone">
      <li>
        <svg viewBox="0 0 16 16" aria-hidden="true"><path fill="#86c524" d="M3.6 1.2 5.8 3.4c.4.4.4 1 0 1.4L4.7 5.9c.8 1.9 2.3 3.4 4.2 4.2l1.1-1.1c.4-.4 1-.4 1.4 0l2.2 2.2c.4.4.4 1 0 1.4l-1.2 1.2c-.8.8-2 1-3 .5C5.8 12.9 3.1 10.2 1.7 6.6c-.5-1-.3-2.2.5-3z"/></svg>
        055-210 384 617
      </li>
      <li>
        <svg viewBox="0 0 16 16" aria-hidden="true"><rect x="3.5" y="0.8" width="9" height="14.4" rx="1.5" fill="none" stroke="#86c524" stroke-width="1.4"/><circle cx="8" cy="12.7" r="0.9" fill="#86c524"/></svg>
        055-734 902 158
      </li>
    </ul>

    <ul class="contacts contacts-web">
      <li>
        hello@ridgemont.build
        <svg viewBox="0 0 16 16" aria-hidden="true"><rect x="0.5" y="3" width="15" height="10" fill="#86c524"/><path d="M0.8 3.4 8 9l7.2-5.6" fill="none" stroke="#fff" stroke-width="1.2"/></svg>
      </li>
      <li>
        www.ridgemont.build
        <svg viewBox="0 0 16 16" aria-hidden="true"><g fill="none" stroke="#86c524" stroke-width="1.3"><circle cx="8" cy="8" r="6.8"/><ellipse cx="8" cy="8" rx="3" ry="6.8"/><path d="M1.2 8h13.6M2.3 4.5h11.4M2.3 11.5h11.4"/></g></svg>
      </li>
    </ul>

    <div class="edge-band"></div>
  </section>

  <section class="card card-back" aria-label="Card back">
    <div class="brand"><span class="brand-mark"></span>Ridgemont</div>
    <div class="edge-band"></div>
  </section>
</body>
</html>
```